Birchvale Gundogs

create website page for Labrador Retriever stud dog business.

Target Market(s)

Owners looking to breed their dogs that compete in NFS/PTL hunt tests.

Industry/Entity Type

Dog Training

Logo Text

Birchvale Gundogs - Stud Dogs

Number of Pages Required

1 page

Colors

Designer to choose colors to be used in the design.

Requirements
Must have
• link to or info from my dogs pedigree.
• Main dog I'm advertising. GRCH Zeke's Jump 5 Rounds FX
• http://www.fieldpuplineage.example/lineage.asp?id=71926
• also link to gundog tallies-- for pass information.
• Can update the pictures to that actual pictures once design is complete.

```html
<!DOCTYPE html>
<html lang="en">
<head>
<meta charset="utf-8">
<title>Birchvale Gundogs – Stud Dogs</title>
<link href="https://fonts.googleapis.com/css2?family=Poppins:wght@300;400;500;600;700&family=Open+Sans:wght@400;600&display=swap" rel="stylesheet">
<style>
:root{
  --red:#a41c1c;
  --red-dark:#8e1616;
  --gold:#c98f0b;
  --ink:#333333;
  --muted:#555555;
  --card:#2e323b;
  --footer:#262626;
  --white:#ffffff;
}
*{margin:0;padding:0;box-sizing:border-box}
html,body{width:1200px;height:2683px;overflow:hidden}
body{position:relative;font-family:"Open Sans",Arial,sans-serif;color:var(--ink);background:var(--white)}
.abs{position:absolute}

/* header */
.site-header{position:absolute;left:0;top:0;width:1200px;height:80px;background:var(--white)}
.brand{position:absolute;left:86px;top:22px;font-family:"Poppins",sans-serif;font-weight:700;font-size:28px;color:var(--red);letter-spacing:.5px}
.main-nav{position:absolute;right:86px;top:30px;display:flex;gap:0;font-family:"Poppins",sans-serif;font-size:13px;color:#444}
.main-nav span{margin-left:26px}

/* hero */
.hero{position:absolute;left:0;top:80px;width:1200px;height:395px;background:linear-gradient(180deg,#6f8a9b 0%,#3f5a52 35%,#2b3b3f 55%,#3a5870 80%,#2d4456 100%)}
.hero-title{position:absolute;left:0;top:145px;width:1200px;text-align:center;font-family:"Poppins",sans-serif;font-size:31px;line-height:46px;color:var(--white)}
.slider-dots{position:absolute;left:1152px;top:154px;display:flex;flex-direction:column;gap:6px}
.slider-dots i{display:block;width:14px;height:14px;border:2px solid var(--white);border-radius:50%}
.slider-dots i.active{background:var(--red)}

/* search */
.search-bar{position:absolute;left:0;top:475px;width:1200px;height:108px;background:var(--red)}
.field{position:absolute;top:26px;width:216px}
.field label{display:block;font-family:"Poppins",sans-serif;font-size:12px;color:var(--white);margin-bottom:5px;text-transform:uppercase}
.select{position:relative;height:32px;background:var(--white);font-size:12px;color:#333;padding:8px 14px}
.select svg{position:absolute;right:18px;top:13px}
.search-btn{position:absolute;left:846px;top:32px;width:202px;height:46px;background:var(--gold);color:var(--white);font-family:"Poppins",sans-serif;font-size:14px;text-align:center;line-height:46px}

/* welcome */
.welcome{position:absolute;left:0;top:583px;width:1200px;height:510px}
.welcome-kicker{position:absolute;left:86px;top:74px;font-family:"Poppins",sans-serif;font-weight:500;font-size:24px;color:var(--ink)}
.welcome-title{position:absolute;left:86px;top:106px;font-family:"Poppins",sans-serif;font-weight:500;font-size:30px;color:var(--ink)}
.welcome-text{position:absolute;left:86px;top:160px;width:516px;font-size:12.4px;line-height:21px;color:var(--muted)}
.welcome-text p+p{margin-top:21px}
.btn-red{position:absolute;background:var(--red);color:var(--white);font-family:"Poppins",sans-serif;text-align:center}
.read-more{left:86px;top:377px;width:150px;height:47px;line-height:47px;font-size:12px;box-shadow:4px 6px 10px rgba(0,0,0,.3)}
.video{position:absolute;left:646px;top:79px;width:466px;height:280px;background:#111}
.video-frame{position:absolute;left:0;top:24px;width:466px;height:226px;background:linear-gradient(135deg,#e0a020 0%,#c9781a 45%,#8c5a1e 70%,#d9a63a 100%)}
.video-play{position:absolute;left:210px;top:114px}
.video-bar{position:absolute;left:0;bottom:0;width:466px;height:30px;background:#1b1b1b}
.video-progress{position:absolute;left:10px;top:4px;width:446px;height:3px;background:#555}

/* featured */
.featured{position:absolute;left:0;top:1093px;width:1200px;height:574px;background:linear-gradient(180deg,#3b2c22 0%,#2c3321 45%,#33461f 75%,#2a3a1b 100%)}
.section-title-light{position:absolute;left:0;top:58px;width:1200px;text-align:center;font-family:"Poppins",sans-serif;font-weight:500;font-size:34px;color:var(--white)}
.dog-card{position:absolute;top:141px;width:230px}
.dog-photo{width:230px;height:220px;border-radius:3px}
.dog-name{margin-top:24px;text-align:center;font-family:"Poppins",sans-serif;font-size:22px;color:#e8e8e8}
.view-more{left:510px;top:453px;width:180px;height:55px;line-height:55px;font-size:16px}

/* faq */
.faq{position:absolute;left:0;top:1667px;width:1200px;height:656px}
.section-title{position:absolute;left:0;top:95px;width:1200px;text-align:center;font-family:"Poppins",sans-serif;font-weight:500;font-size:34px;color:var(--ink)}
.faq-item{position:absolute;width:501px;background:var(--card);color:var(--white);border-radius:2px;box-shadow:0 2px 4px rgba(0,0,0,.25)}
.faq-item.open{background:var(--red)}
.faq-q{position:relative;padding:27px 60px 0 30px;font-family:"Poppins",sans-serif;font-size:15px}
.faq-item.open .faq-q{padding-top:30px}
.faq-a{padding:10px 40px 0 30px;font-size:11.3px;line-height:18px}
.toggle{position:absolute;right:28px;top:30px;width:15px;height:15px;border:1.5px solid var(--white);border-radius:2px}
.toggle:before{content:"";position:absolute;left:2px;top:5.5px;width:8px;height:1.5px;background:var(--white)}
.toggle.plus:after{content:"";position:absolute;left:5.3px;top:2px;width:1.5px;height:8px;background:var(--white)}

/* footer */
.site-footer{position:absolute;left:0;top:2323px;width:1200px;height:270px;background:var(--footer);color:var(--white)}
.footer-brand{position:absolute;left:86px;top:90px;font-family:"Poppins",sans-serif;font-weight:700;font-size:25px;color:var(--white)}
.social{position:absolute;left:86px;top:140px;display:flex;gap:6px}
.social i{display:block;width:21px;height:21px;border-radius:50%;background:#5b6270}
.contact{position:absolute;left:420px;font-family:"Poppins",sans-serif;font-size:16px;display:flex;align-items:center;gap:18px}
.footer-heading{position:absolute;top:50px;font-family:"Poppins",sans-serif;font-size:17px}
.footer-links{position:absolute;left:712px;top:88px;list-style:none;font-family:"Poppins",sans-serif;font-size:12.5px;line-height:27px}
.footer-links li:before{content:"> ";}
.email-input{position:absolute;left:920px;top:89px;width:190px;height:41px;border:1px solid #aaa;font-size:12px;padding:12px 14px}
.signup{left:920px;top:147px;width:103px;height:42px;line-height:42px;font-size:16px}
.copyright{position:absolute;left:0;top:2593px;width:1200px;height:90px;background:var(--red);color:var(--white);text-align:center;font-size:14px;line-height:90px}
</style>
</head>
<body>

<header class="site-header">
  <div class="brand">Birchvale Gundogs</div>
  <nav class="main-nav">
    <span>Home</span><span>Terms/Condition</span><span>Classifieds</span><span>Advertise</span><span>Help/Stats</span><span>Stud Dog Finder</span><span>My Account</span><span>Login</span>
  </nav>
</header>

<section class="hero" role="img" aria-label="Black Labrador retriever splashing out of a lake with a ball in its mouth">
  <h1 class="hero-title">Anyone can search pedigrees<br>litters, stud dogs,etc</h1>
  <div class="slider-dots"><i></i><i></i><i class="active"></i><i></i></div>
</section>

<section class="search-bar">
  <div class="field" style="left:150px"><label>Breed:</label><div class="select">Labrador Retriever<svg width="8" height="5"><path d="M0 0H8L4 5Z" fill="#333"/></svg></div></div>
  <div class="field" style="left:380px"><label>Location:</label><div class="select">Doesn't Matter<svg width="8" height="5"><path d="M0 0H8L4 5Z" fill="#333"/></svg></div></div>
  <div class="field" style="left:614px"><label>Color:</label><div class="select">Doesn't Matter<svg width="8" height="5"><path d="M0 0H8L4 5Z" fill="#333"/></svg></div></div>
  <div class="search-btn">SEARCH</div>
</section>

<section class="welcome">
  <div class="welcome-kicker">WELCOME TO</div>
  <h2 class="welcome-title">BIRCHVALE GUNDOGS</h2>
  <div class="welcome-text">
    <p>Lorem Ipsum is simply dummy text of the printing and typesetting industry. Lorem Ipsum has been the industry's standard dummy text ever since the 1500s, when an unknown printer took a galley of type and scrambled it to make a type specimen book. It has survived not only five centuries.</p>
    <p>But also the leap into electronic typesetting, remaining essentially unchanged. It was popularised in the 1960s with the release of Typecraft sheets containing Lorem Ipsum passages, and more recently with desktop publishing software like Layout Studio including versions of Lorem Ipsum.</p>
  </div>
  <div class="btn-red read-more">READ MORE &gt;</div>
  <div class="video">
    <div class="video-frame" role="img" aria-label="Video still of a black Labrador lying in autumn leaves"></div>
    <svg class="video-play" width="46" height="46"><circle cx="23" cy="23" r="22" fill="rgba(0,0,0,.55)"/><path d="M18 14L33 23L18 32Z" fill="#fff"/></svg>
    <div class="video-bar"><div class="video-progress"></div>
      <svg class="abs" style="left:12px;top:12px" width="10" height="12"><path d="M0 0L10 6L0 12Z" fill="#ccc"/></svg>
    </div>
  </div>
</section>

<section class="featured" role="img" aria-label="Background of several Labrador retrievers in tall grass">
  <h2 class="section-title-light">FEATURED DOG</h2>
  <div class="dog-card" style="left:86px"><div class="dog-photo" role="img" aria-label="Chocolate Labrador sitting in a garden" style="background:linear-gradient(160deg,#4f6b2e,#5a4838 60%,#3b3128)"></div><div class="dog-name">Clara Whitfield</div></div>
  <div class="dog-card" style="left:353px"><div class="dog-photo" role="img" aria-label="Black Labrador retrieving a pheasant" style="background:linear-gradient(160deg,#3f6fa0,#1f2428 55%,#7a4a2a)"></div><div class="dog-name">Lorem Ipsum</div></div>
  <div class="dog-card" style="left:617px"><div class="dog-photo" role="img" aria-label="Black Labrador leaping out of water" style="background:linear-gradient(160deg,#c2a277,#2a2622 55%,#a68a63)"></div><div class="dog-name">Lorem Ipsum</div></div>
  <div class="dog-card" style="left:883px"><div class="dog-photo" role="img" aria-label="Black Labrador portrait on a golden background" style="background:linear-gradient(160deg,#d9b270,#26221f 55%,#c89d58)"></div><div class="dog-name">Lorem Ipsum</div></div>
  <div class="btn-red view-more">View More</div>
</section>

<section class="faq">
  <h2 class="section-title">FAQ</h2>
  <div class="faq-item open" style="left:86px;top:166px;height:160px">
    <div class="faq-q">What's the purpose of Field Pup Lineage?<span class="toggle"></span></div>
    <div class="faq-a">The purpose of Field Pup Lineage is to provide working and hunting Labrador retriever owners an educational and resourceful research pedigree database. It also provides owners a way to research what the accomplishments of related dogs. Plus since PTL and NFS do not recognize</div>
  </div>
  <div class="faq-item" style="left:86px;top:338px;height:80px"><div class="faq-q">Why are their only certain breeds on this site?<span class="toggle plus"></span></div></div>
  <div class="faq-item" style="left:86px;top:428px;height:82px"><div class="faq-q">Why do I see duplicates dogs?<span class="toggle plus"></span></div></div>

  <div class="faq-item" style="left:612px;top:166px;height:80px"><div class="faq-q">Can I add my Labrador Retriever?<span class="toggle plus"></span></div></div>
  <div class="faq-item" style="left:612px;top:257px;height:80px"><div class="faq-q">How do I add a Labrador retriever's name?<span class="toggle plus"></span></div></div>
  <div class="faq-item" style="left:612px;top:348px;height:160px">
    <div class="faq-q">Why do I need to register to add or edit dog's?<span class="toggle"></span></div>
    <div class="faq-a">This is a protection for the database and the hard work that everyone has put into it. If you feel that someone is abusing the database please email me at report@fieldpuplineage.example (please include dog's name that has been changed)</div>
  </div>
</section>

<footer class="site-footer">
  <div class="footer-brand">Birchvale Gundogs</div>
  <div class="social"><i></i><i></i><i></i><i></i><i></i></div>
  <div class="contact" style="top:63px"><svg width="14" height="14" viewBox="0 0 24 24"><path d="M6.6 10.8a15 15 0 0 0 6.6 6.6l2.2-2.2c.3-.3.7-.4 1-.2 1.1.4 2.3.6 3.6.6.6 0 1 .4 1 1V20c0 .6-.4 1-1 1A17 17 0 0 1 3 4c0-.6.4-1 1-1h3.5c.6 0 1 .4 1 1 0 1.3.2 2.5.6 3.6.1.3 0 .7-.2 1z" fill="#fff"/></svg>+123 456 789</div>
  <div class="contact" style="top:111px"><svg width="15" height="12" viewBox="0 0 15 12"><rect width="15" height="12" rx="1" fill="#fff"/><path d="M0 1L7.5 7L15 1" stroke="#262626" stroke-width="1.4" fill="none"/></svg>info@company.com</div>
  <div class="footer-heading" style="left:712px">Info</div>
  <ul class="footer-links"><li>Home</li><li>Terms/Condition</li><li>Classifieds</li><li>Advertise</li><li>Help/Stats</li><li>Stud Dog Finder</li></ul>
  <div class="footer-heading" style="left:918px">Stay in touch</div>
  <div class="email-input">Enter your email</div>
  <div class="btn-red signup">SIGN UP</div>
</footer>

<div class="copyright">Copyright (c) 2017. Birchvale Gundogs. All rights reserved.</div>

</body>
</html>
```